Graphic Design for Application Form and Menu

We are a success education company called Marwick Trellis. We are designing a USB application for a personal development program that will be cross platform (PC/Mac). The product is called Quiet Harbor, Lantern Academy (These logos are already created). The program will open pdf books in a Flash reader, play audio and video files in the default media player, and open windows for recording entries in a journal and for setting goals.
We need a graphic design for a small control panel (300px X 300px) to launch the different modules of the program.

We are looking for a design that is clean and professional.
A sample is included of everything that needs to be on the form. A sample menu is also included. We are looking for other designs for the form and menu.
Updates

Industry/Entity Type

Graphic Design

Requirements
Must have
• The panel will have: a menu, two toolbars, and two status panels.
ItemDetails:
A menu will have items for "Welcome, Profile, and Kudos."
One tool bar will have items for "Guidebooks (w/9 item popup menu), Audios (w/9 item popup menu), Videos (w/9 item popup menu), Journal (w/2 item popup menu), and Goals."
A second tool bar will have items for "Blog, Community, Events, Sovereignty, Foundation, and Influence."
The tool bars should have icons and text.
There should be two status panel, one for Audio and one for Video.
The status panels should show the name of the audio or video that is opened, have check boxes for: Add to favorites, Come back, and Done, and have links for: Audios, Top Posts, Post, and Tips.

```html
<!DOCTYPE html>
<html lang="en">
<head>
<meta charset="utf-8">
<title>Marwick Trellis · Quiet Harbor Control Panel</title>
<link href="https://fonts.googleapis.com/css2?family=Arimo:wght@400;700&display=swap" rel="stylesheet">
<style>
  :root {
    --sky: #16b4ea;
    --sky-line: #2aaee0;
    --window-bg: #ffffff;
    --page-bg: #f3f5f7;
    --panel-grey: #d6d6d6;
    --pill-text: #c2c2c2;
    --label-grey: #555555;
    --icon-dark: #111111;
    --close-pink: #f7d9dc;
    --close-red: #d9323e;
  }
  * { box-sizing: border-box; margin: 0; padding: 0; }
  html, body { width: 1200px; height: 1200px; overflow: hidden; }
  body { background: var(--page-bg); font-family: "Arimo", Arial, sans-serif; position: relative; }

  .control-window {
    position: absolute; left: 16px; top: 16px; width: 1164px; height: 1164px;
    background: var(--window-bg); border: 3px solid var(--sky-line); border-radius: 40px;
    box-shadow: 8px 10px 0 #2b2b2b, 10px 14px 16px rgba(0,0,0,.35);
  }
  .close-button {
    position: absolute; left: 1084px; top: 6px; width: 46px; height: 46px; border-radius: 50%;
    background: radial-gradient(circle at 40% 35%, #fff, var(--close-pink) 70%);
    border: 2px solid #c8b4b8;
  }
  .close-button svg { position: absolute; left: 11px; top: 11px; }

  .main-menu { position: absolute; top: 38px; left: 0; width: 100%; }
  .main-menu span { position: absolute; font-size: 48px; color: var(--sky); white-space: nowrap; }

  .toolbar {
    position: absolute; left: 34px; width: 1070px; height: 162px;
    border: 3px solid var(--sky-line); border-radius: 52px;
    background: linear-gradient(#ffffff 0%, #fafafa 55%, #e7e7e7 100%);
    overflow: hidden;
  }
  .toolbar-modules { top: 116px; }
  .toolbar-community { top: 956px; }
  .tool { position: absolute; top: 0; height: 100%; text-align: center; }
  .toolbar-modules .tool + .tool { border-left: 2px solid #9fd3ea; }
  .tool svg { position: absolute; left: 50%; transform: translateX(-50%); top: 20px; }
  .tool-label { position: absolute; left: 0; right: 0; top: 108px; font-size: 26px; color: var(--label-grey); letter-spacing: .5px; }
  .toolbar-community .tool-label { top: 112px; font-size: 27px; color: #333; }
  .badge { position: absolute; left: 50%; top: 22px; width: 74px; height: 74px; margin-left: -37px; border-radius: 10px; box-shadow: 1px 2px 3px rgba(0,0,0,.3); }

  .status-heading { position: absolute; top: 304px; width: 456px; text-align: center; font-size: 38px; color: var(--sky); }

  .status-panel {
    position: absolute; top: 372px; width: 456px; height: 534px; border-radius: 24px;
    background: var(--panel-grey); box-shadow: 6px 8px 10px rgba(0,0,0,.35);
  }
  .now-playing { position: absolute; left: 20px; top: 32px; width: 410px; height: 76px; border-radius: 22px; background: var(--sky); }
  .status-toggle {
    position: absolute; left: 22px; width: 402px; height: 58px; border-radius: 29px;
    border: 2px solid #9fd7ef; background: linear-gradient(#ffffff, #eeeeee);
    font-size: 38px; line-height: 54px; text-align: center; color: var(--pill-text);
  }
  .status-link { position: absolute; font-size: 32px; color: var(--sky); text-decoration: underline; }
</style>
</head>
<body>
<main class="control-window">
  <div class="close-button">
    <svg width="22" height="22" viewBox="0 0 22 22"><path d="M4 4 L18 18 M18 4 L4 18" stroke="var(--close-red)" stroke-width="3" stroke-linecap="round"/></svg>
  </div>

  <nav class="main-menu">
    <span style="left:54px">Welcome</span>
    <span style="left:338px">Profile</span>
    <span style="left:544px">Kudos</span>
  </nav>

  <section class="toolbar toolbar-modules">
    <div class="tool" style="left:0;width:258px">
      <svg width="84" height="76" viewBox="0 0 84 76" fill="#fff" stroke="#222" stroke-width="3" stroke-linejoin="round">
        <path d="M42 22 C30 10 14 10 6 16 L12 64 C22 58 34 60 42 70 Z"/>
        <path d="M42 22 C54 10 70 10 78 16 L72 64 C62 58 50 60 42 70 Z"/>
        <path d="M42 22 L42 70"/>
      </svg>
      <div class="tool-label">GuideBook</div>
    </div>
    <div class="tool" style="left:258px;width:190px">
      <svg width="84" height="76" viewBox="0 0 84 76">
        <path d="M6 26 H22 L42 8 V68 L22 50 H6 Z" fill="var(--icon-dark)"/>
        <path d="M52 26 Q60 38 52 50 M60 18 Q74 38 60 58 M68 10 Q88 38 68 66" fill="none" stroke="var(--icon-dark)" stroke-width="4" stroke-linecap="round"/>
      </svg>
      <div class="tool-label">Audios</div>
    </div>
    <div class="tool" style="left:448px;width:200px">
      <svg width="90" height="76" viewBox="0 0 90 76">
        <rect x="4" y="12" width="60" height="52" fill="var(--icon-dark)"/>
        <path d="M64 32 L86 16 V60 L64 44 Z" fill="var(--icon-dark)"/>
      </svg>
      <div class="tool-label">Videos</div>
    </div>
    <div class="tool" style="left:648px;width:182px">
      <svg width="84" height="80" viewBox="0 0 84 80">
        <rect x="6" y="4" width="72" height="72" rx="10" fill="#8a8a8a" stroke="#333" stroke-width="3"/>
        <rect x="14" y="12" width="56" height="56" rx="4" fill="#e6e6e6"/>
        <path d="M24 58 L30 42 L56 16 L64 24 L38 50 Z" fill="#fff" stroke="#222" stroke-width="3" stroke-linejoin="round"/>
        <path d="M24 58 L38 50" stroke="#222" stroke-width="3"/>
      </svg>
      <div class="tool-label">Journal</div>
    </div>
    <div class="tool" style="left:830px;width:240px">
      <svg width="84" height="80" viewBox="0 0 84 80">
        <rect x="6" y="6" width="72" height="68" rx="6" fill="var(--icon-dark)"/>
        <path d="M14 62 L30 38 L44 50 L68 18" fill="none" stroke="#fff" stroke-width="4" stroke-linejoin="round"/>
        <path d="M14 68 L32 48 L46 58 L70 30" fill="none" stroke="#fff" stroke-width="3" stroke-linejoin="round"/>
      </svg>
      <div class="tool-label">Goals</div>
    </div>
  </section>

  <h2 class="status-heading" style="left:61px;font-weight:400">Audio</h2>
  <h2 class="status-heading" style="left:619px;font-weight:400">Video</h2>

  <section class="status-panel" style="left:61px">
    <div class="now-playing"></div>
    <div class="status-toggle" style="top:134px">Come Back</div>
    <div class="status-toggle" style="top:200px">Add to Favorites</div>
    <div class="status-toggle" style="top:268px">Done</div>
    <span class="status-link" style="left:36px;top:360px">Audios</span>
    <span class="status-link" style="left:340px;top:358px">Post</span>
    <span class="status-link" style="left:36px;top:440px">Top Posts</span>
    <span class="status-link" style="left:346px;top:438px">Tips</span>
  </section>

  <section class="status-panel" style="left:619px">
    <div class="now-playing"></div>
    <div class="status-toggle" style="top:134px">Come Back</div>
    <div class="status-toggle" style="top:200px">Add to Favorites</div>
    <div class="status-toggle" style="top:268px">Done</div>
    <span class="status-link" style="left:36px;top:360px">Audios</span>
    <span class="status-link" style="left:340px;top:358px">Post</span>
    <span class="status-link" style="left:36px;top:440px">Top Posts</span>
    <span class="status-link" style="left:346px;top:438px">Tips</span>
  </section>

  <section class="toolbar toolbar-community">
    <div class="tool" style="left:40px;width:160px">
      <div class="badge" style="background:linear-gradient(#f59a52,#d8561a)"></div>
      <div class="tool-label">Blog</div>
    </div>
    <div class="tool" style="left:180px;width:200px">
      <div class="badge" style="background:linear-gradient(#b8f0f8,#7fd5e6)"></div>
      <div class="tool-label">Community</div>
    </div>
    <div class="tool" style="left:336px;width:160px">
      <div class="badge" style="background:linear-gradient(#f7d36a,#c98a1e)"></div>
      <div class="tool-label">Events</div>
    </div>
    <div class="tool" style="left:480px;width:200px">
      <div class="badge" style="background:linear-gradient(#a070e0,#5a2a9a)"></div>
      <div class="tool-label">Sovereignty</div>
    </div>
    <div class="tool" style="left:678px;width:200px">
      <div class="badge" style="background:linear-gradient(#d8723a,#8a1e10)"></div>
      <div class="tool-label">Foundation</div>
    </div>
    <div class="tool" style="left:858px;width:200px">
      <div class="badge" style="background:linear-gradient(#3a3a3a,#000)"></div>
      <div class="tool-label">Influence</div>
    </div>
  </section>
</main>
</body>
</html>
```